eCommerce website for a DIY shop & communal center

We need a website for a business called The Maple Bench. The Maple Bench is both a shop and communal establishment where people with shared interests, especially in DIY (Do It Yourself) and crafting, can gather to shop for & work on projects while sharing ideas, equipment, supplies and knowledge. The shop is both brick & motor and online. The physical communal space provides workstations, equipment, tools and supplies and expertise for DIY lovers to create their projects.

Target Market(s)

Middle & upper class DIY enthusiasts, creative hobbyists, budding artists & small business owners

Industry/Entity Type

DIY, Arts & Crafts

Coding

Coded - Design and coding required

Number of Pages Required

5+ page

Requirements
Must have
• Menus to include 1. home page (with about us, operating hours, contacts, location, meet the team); 2. Bench activities (how to DIY at the Bench, booking, equipment & tools, house rules); 3. Bench events (events in the Bench, offsite events); 4. Resources (FAQs, tutorials, blogs, eBooks) and 5. Online shop
Nice to have
• Branding guidelines eg logo colours (see attachment) to influence design. Tillpost shop. Booking feature for activities & events at the Bench.

```html
<!DOCTYPE html>
<html lang="en">
<head>
<meta charset="utf-8">
<title>Bench Events – The Maple Bench</title>
<link href="https://fonts.googleapis.com/css2?family=Roboto:wght@400;500;700;900&family=Dancing+Script:wght@600&display=swap" rel="stylesheet">
<style>
:root{
  --blue:#2a9fd8;
  --orange:#f47b20;
  --ink:#222;
  --muted:#777;
  --page:#eef0f2;
  --tint:#def1fb;
  --footer:#121212;
  --footer-text:#cfcfcf;
  --white:#fff;
}
*{box-sizing:border-box;margin:0;padding:0}
html,body{width:721px;height:1200px;overflow:hidden}
body{font-family:"Roboto",Arial,sans-serif;color:var(--ink);background:var(--white);position:relative}

.topbar{height:34px;background:var(--white);display:flex;align-items:center;justify-content:space-between;padding:0 40px;border-bottom:1px solid #e6e6e6;font-size:11px}
.topbar .phone{display:flex;align-items:center;gap:6px}
.social{display:flex;gap:5px}
.social span{width:18px;height:18px;border:1px solid #999;border-radius:50%;display:block}

.nav{height:28px;background:var(--white);display:flex;align-items:center;justify-content:center;font-size:9.5px;font-weight:700;letter-spacing:.2px;position:relative;z-index:2}
.nav a{color:var(--ink);text-decoration:none;padding:0 13px}
.nav a.active{color:var(--orange)}
.nav .gap{width:112px}
.brand{position:absolute;left:50%;top:-30px;transform:translateX(-50%);width:100px;height:100px;border-radius:50%;background:var(--white);display:flex;align-items:center;justify-content:center;text-align:center;font-size:14px;font-weight:700;color:var(--orange);line-height:1.1;padding-top:6px}

.hero{height:202px;background:linear-gradient(100deg,#6b4a2e 0%,#b48a5e 40%,#d9c3a2 70%,#8c6a46 100%);position:relative}
.hero h1{position:absolute;left:40px;top:84px;color:var(--white);font-size:34px;font-weight:900;letter-spacing:.5px}

.events-area{background:var(--page);height:696px;padding:22px 34px 0}
.events-card{background:var(--white);padding:30px 19px 20px}
.events-card h2{font-family:"Dancing Script",cursive;font-size:27px;font-weight:600;text-align:center;color:var(--orange);line-height:1.2}
.events-card h2 em{font-style:normal;color:var(--blue)}
.intro{text-align:center;font-size:8.5px;color:var(--muted);line-height:1.5;margin:8px auto 20px;width:320px}

.event{display:flex;height:138px;margin-bottom:16px;background:var(--white);box-shadow:0 1px 4px rgba(0,0,0,.12)}
.event:last-child{margin-bottom:0}
.date{width:91px;background:var(--tint);padding:20px 0 0 16px;color:var(--blue)}
.date .day{font-size:28px;font-weight:700;line-height:1}
.date .month{font-size:10px;margin-top:4px}
.date .year{font-size:10px}
.date .range{font-size:7px;color:var(--muted);margin-top:14px;line-height:1.5}
.photo{width:125px}
.info{flex:1;padding:18px 12px 0}
.info h3{font-size:12.5px;font-weight:700;line-height:1.25;margin-bottom:8px}
.info p{font-size:8px;color:var(--muted);line-height:1.5}
.info .more{font-size:7.5px;color:var(--orange);margin-top:8px;display:block}
.price{width:127px;background:var(--tint);text-align:center;padding-top:22px}
.price .amount{font-size:19px;font-weight:700}
.price .label{font-size:10px;font-weight:700;margin-top:10px}
.price svg{margin-top:8px}
.price .addr{font-size:7px;color:var(--muted);line-height:1.4;margin-top:3px}

.buttons{display:flex;justify-content:center;gap:24px;margin-top:26px}
.btn{width:112px;height:28px;border-radius:14px;color:var(--white);font-size:9px;font-weight:700;display:flex;align-items:center;justify-content:center}
.btn.upcoming{background:var(--orange)}
.btn.past{background:var(--blue)}

.footer{background:var(--footer);height:240px;padding:32px 60px 0;color:var(--footer-text);position:relative}
.cols{display:flex;gap:28px}
.col h4{color:var(--white);font-size:10px;font-weight:700;margin-bottom:8px}
.col li{list-style:none;font-size:8.5px;line-height:1.75}
.col.about{width:60px}.col.offer{width:72px}.col.other{width:60px}.col.contact{width:112px}
.subscribe input{width:150px;height:22px;border:0;border-radius:11px;padding:0 10px;font-size:8px;font-family:inherit}
.subscribe .go{width:150px;height:22px;border-radius:11px;background:var(--orange);color:var(--white);font-size:9px;font-weight:700;display:flex;align-items:center;justify-content:center;margin-top:7px}
.subscribe .social{justify-content:center;margin-top:10px;width:150px}
.subscribe .social span{background:var(--white);border:0}
.copyright{position:absolute;left:0;right:0;bottom:0;height:36px;border-top:1px solid #2c2c2c;text-align:center;font-size:8px;line-height:36px;color:#aaa}
</style>
</head>
<body>

<header>
  <div class="topbar">
    <div class="phone">
      <svg width="10" height="10" viewBox="0 0 24 24"><path fill="#222" d="M6.6 10.8a15.1 15.1 0 0 0 6.6 6.6l2.2-2.2a1 1 0 0 1 1-.25 11.4 11.4 0 0 0 3.6.57 1 1 0 0 1 1 1V20a1 1 0 0 1-1 1A17 17 0 0 1 3 4a1 1 0 0 1 1-1h3.5a1 1 0 0 1 1 1c0 1.25.2 2.450.57 3.57a1 1 0 0 1-.25 1z"/></svg>
      <span>888 - 888 - 8888</span>
    </div>
    <div class="social"><span></span><span></span><span></span><span></span></div>
  </div>
  <nav class="nav">
    <a href="#">HOME</a>
    <a href="#">BENCH ACTIVITIES</a>
    <a href="#" class="active">BENCH EVENTS</a>
    <span class="gap"></span>
    <a href="#">RESOURCES</a>
    <a href="#">ONLINE SHOP</a>
    <a href="#">CONTACT US</a>
    <div class="brand">The Maple<br>Bench</div>
  </nav>
</header>

<section class="hero" role="img" aria-label="Workshop bench with a mitre saw and wood shavings">
  <h1>BENCH EVENTS</h1>
</section>

<main class="events-area">
  <div class="events-card">
    <h2>Workshops Organized <em>By The Bench</em></h2>
    <p class="intro">The Maple Bench organizes a variety of workshops. These are listed within the Bench events. Find upcoming events below.</p>

    <article class="event">
      <div class="date"><div class="day">13</div><div class="month">July</div><div class="year">2021</div><div class="range">July 13<br>July 18</div></div>
      <div class="photo" role="img" aria-label="Crafters working on a painted project" style="background:linear-gradient(135deg,#7aa7c4,#c9a77a,#5b7f5a)"></div>
      <div class="info">
        <h3>The standard Lorem Ipsum passage, used since the 1500s</h3>
        <p>Lorem ipsum dolor sit amet, consectetur adipiscing elit, sed do eiusmod tempor incididunt ut labore et dolore magna aliqua. Quis ipsum suspendisse ultrices gravida.</p>
        <span class="more">Find out more »</span>
      </div>
      <div class="price">
        <div class="amount">$30.00</div>
        <div class="label">Suitable</div>
        <svg width="10" height="13" viewBox="0 0 24 32"><path fill="#2a9fd8" d="M12 0a12 12 0 0 0-12 12c0 9 12 20 12 20s12-11 12-20A12 12 0 0 0 12 0zm0 17a5 5 0 1 1 0-10 5 5 0 0 1 0 10z"/></svg>
        <div class="addr">48 Timber Lane<br>Oakridge, 1234567</div>
      </div>
    </article>

    <article class="event">
      <div class="date"><div class="day">13</div><div class="month">July</div><div class="year">2021</div><div class="range">July 13<br>July 18</div></div>
      <div class="photo" role="img" aria-label="Group gathered around a workbench" style="background:linear-gradient(135deg,#8a6b4f,#c8b08e,#6d8ea0)"></div>
      <div class="info">
        <h3>The standard Lorem Ipsum passage, used since the 1500s</h3>
        <p>Lorem ipsum dolor sit amet, consectetur adipiscing elit, sed do eiusmod tempor incididunt ut labore et dolore magna aliqua. Quis ipsum suspendisse ultrices gravida.</p>
        <span class="more">Find out more »</span>
      </div>
      <div class="price">
        <div class="amount">$30.00</div>
        <div class="label">Suitable</div>
        <svg width="10" height="13" viewBox="0 0 24 32"><path fill="#2a9fd8" d="M12 0a12 12 0 0 0-12 12c0 9 12 20 12 20s12-11 12-20A12 12 0 0 0 12 0zm0 17a5 5 0 1 1 0-10 5 5 0 0 1 0 10z"/></svg>
        <div class="addr">48 Timber Lane<br>Oakridge, 1234567</div>
      </div>
    </article>

    <article class="event">
      <div class="date"><div class="day">13</div><div class="month">July</div><div class="year">2021</div><div class="range">July 13<br>July 18</div></div>
      <div class="photo" role="img" aria-label="Workshop class building a wooden item" style="background:linear-gradient(135deg,#5f6f4e,#b59a76,#8c8c8c)"></div>
      <div class="info">
        <h3>The standard Lorem Ipsum passage, used since the 1500s</h3>
        <p>Lorem ipsum dolor sit amet, consectetur adipiscing elit, sed do eiusmod tempor incididunt ut labore et dolore magna aliqua. Quis ipsum suspendisse ultrices gravida.</p>
        <span class="more">Find out more »</span>
      </div>
      <div class="price">
        <div class="amount">$30.00</div>
        <div class="label">Suitable</div>
        <svg width="10" height="13" viewBox="0 0 24 32"><path fill="#2a9fd8" d="M12 0a12 12 0 0 0-12 12c0 9 12 20 12 20s12-11 12-20A12 12 0 0 0 12 0zm0 17a5 5 0 1 1 0-10 5 5 0 0 1 0 10z"/></svg>
        <div class="addr">48 Timber Lane<br>Oakridge, 1234567</div>
      </div>
    </article>
  </div>

  <div class="buttons">
    <span class="btn upcoming">UPCOMING EVENT</span>
    <span class="btn past">PAST EVENTS</span>
  </div>
</main>

<footer class="footer">
  <div class="cols">
    <div class="col about"><h4>ABOUT</h4><ul><li>Our Story</li><li>Press</li><li>Locations</li><li>Blog</li><li>Contact Us</li></ul></div>
    <div class="col offer"><h4>OUR OFFERING</h4><ul><li>Projects</li><li>Paint Room</li><li>Parties</li><li>Classes</li></ul></div>
    <div class="col other"><h4>OTHER</h4><ul><li>Franchise</li><li>Gift Cards</li><li>FAQ</li><li>Refund Policy</li></ul></div>
    <div class="col contact"><h4>CONTACT US</h4><ul><li>48 Timber Lane Oakridge</li><li>888 - 888 - 8888</li><li>888 - 888 - 8888</li><li>hello@maplebench.com</li></ul></div>
    <div class="col subscribe"><h4>GET UPDATES &amp; PROMOS</h4>
      <input type="text" placeholder="Email Address">
      <div class="go">SUBSCRIBE</div>
      <div class="social"><span></span><span></span><span></span><span></span></div>
    </div>
  </div>
  <div class="copyright">Copyright © 2017 The Maple Bench. All right reserved.</div>
</footer>

</body>
</html>
```